website design for Northvale Electric

A portfolio website for a high end commercial and residential electrical contracting company. The current site northvaleelectric.example does not represent the current direction but the images in the gallery give you an idea of the work we do. Current logo will be uploaded shortly but is black text on white background.
Target Market(s)
General Contractors, Residential Home Owners, clients intersted in Velmora home automation.
Industry/Entity Type
Electrician
Coding
Coded - Design and coding required
Number of Pages Required
2 page
Font styles to use
Sans Serif
Colors
Designer to choose colors to be used in the design.
Requirements
Must have
- Portfolio section highlighting different service areas and products (Velmora Housepilot, etc)

```html
<!DOCTYPE html>
<html lang="en">
<head>
<meta charset="utf-8">
<title>Northvale Electric</title>
<link href="https://fonts.googleapis.com/css2?family=Lora:wght@400;700&family=Open+Sans:wght@400;600;700&display=swap" rel="stylesheet">
<style>
:root{
  --ink:#222;
  --dark:#1f1f1f;
  --footer:#1b1b1b;
  --muted:#666;
  --band:#eeeeee;
  --white:#fff;
  --line:#d6d6d6;
}
*{box-sizing:border-box;margin:0;padding:0}
html,body{width:1200px;height:2200px;overflow:hidden}
body{font-family:"Open Sans",Arial,sans-serif;color:var(--ink);background:var(--white)}

/* header */
.site-header{height:100px;display:flex;align-items:center;justify-content:space-between;padding:0 60px}
.brand{font-family:"Open Sans",Arial,sans-serif;font-weight:700;font-size:38px;color:var(--ink)}
.nav{display:flex;align-items:center;gap:6px;font-size:14px}
.nav a{color:var(--ink);text-decoration:none;padding:10px 16px}
.nav a.active{background:var(--dark);color:var(--white)}
.search{display:flex;margin-left:14px;border:1px solid var(--line)}
.search span{width:150px;padding:9px 10px;color:#999;font-size:13px}
.search i{width:38px;background:#e6e6e6;display:flex;align-items:center;justify-content:center}

/* hero */
.hero{position:relative;height:450px;background:linear-gradient(180deg,#6d8fb0 0%,#3f5a76 45%,#2a2a2e 75%,#3a2c22 100%);display:flex;flex-direction:column;align-items:center;justify-content:center;color:var(--white);text-align:center}
.hero h1{font-family:"Lora",Georgia,serif;font-size:68px;font-weight:700;letter-spacing:1px;margin-bottom:6px}
.hero p{font-size:30px;line-height:1.25;max-width:640px}
.dots{position:absolute;bottom:42px;display:flex;gap:10px}
.dots b{width:10px;height:10px;border-radius:50%;background:rgba(255,255,255,.5)}
.dots b.on{background:var(--white)}

/* welcome */
.welcome{height:280px;text-align:center;padding-top:50px}
.section-title{font-family:"Lora",Georgia,serif;font-size:38px;font-weight:400;margin-bottom:24px}
.welcome p{width:760px;margin:0 auto;font-size:14px;line-height:1.75;color:#444}
.btn{display:inline-block;margin-top:26px;background:var(--dark);color:var(--white);font-family:"Lora",Georgia,serif;font-size:15px;padding:12px 28px}

/* services */
.services{height:385px;background:var(--band);padding-top:40px;text-align:center}
.service-grid{display:grid;grid-template-columns:repeat(3,1fr);gap:44px 40px;width:1040px;margin:18px auto 0;text-align:left}
.service{display:flex;gap:18px}
.service svg{flex:none}
.service h3{font-family:"Lora",Georgia,serif;font-size:24px;font-weight:400;margin-bottom:6px}
.service p{font-size:13px;line-height:1.5;color:#555;width:200px}

/* gallery */
.gallery{height:610px;padding-top:36px;text-align:center}
.gallery .section-title{margin-bottom:16px}
.tabs{display:flex;justify-content:center;gap:6px;margin:0 0 24px;font-size:13px}
.tabs span{padding:6px 12px}
.tabs span.on{background:var(--dark);color:var(--white)}
.photo-grid{display:grid;grid-template-columns:repeat(3,310px);gap:30px 35px;justify-content:center}
.photo{height:200px}

/* footer */
.site-footer{height:380px;background:var(--footer);color:#cfcfcf;padding:38px 70px 0}
.foot-cols{display:flex;justify-content:space-between}
.foot-col h4{font-size:13px;font-weight:600;color:var(--white);letter-spacing:.5px;margin-bottom:12px;text-transform:uppercase}
.foot-col li{list-style:none;font-size:12.5px;line-height:2}
.contact li{display:flex;align-items:center;gap:8px}
.social{display:flex;gap:10px;margin-bottom:18px}
.social b{width:20px;height:20px;border-radius:50%;background:#cfcfcf}
.copy{font-size:12px;line-height:1.6}
</style>
</head>
<body>

<header class="site-header">
  <div class="brand">Northvale Electric</div>
  <nav class="nav">
    <a class="active">Home</a>
    <a>Gallery</a>
    <a>Specialty Services</a>
    <a>About</a>
    <a>Contact</a>
    <div class="search"><span>Search</span><i><svg width="14" height="14" viewBox="0 0 14 14"><circle cx="6" cy="6" r="4.5" fill="none" stroke="#333" stroke-width="1.6"/><line x1="9.3" y1="9.3" x2="13" y2="13" stroke="#333" stroke-width="1.8"/></svg></i></div>
  </nav>
</header>

<section class="hero" role="img" aria-label="Modern residence lit at dusk with warm interior lights">
  <h1>Northvale Electric</h1>
  <p>We are a high end commercial and residential electrical contracting company</p>
  <div class="dots"><b class="on"></b><b></b><b></b></div>
</section>

<section class="welcome">
  <h2 class="section-title">Welcome to Our Website</h2>
  <p>Northvale Electric is a full service electrical contracting shop. We offer commercial, residential, light industrial, and agricultural services. We're Velmora Housepilot and Velmora Motorized Shades certified, as well as an authorized Brightcore generator dealer. We've serviced the Cedar Basin and South Central Valley area for over 40 years.</p>
  <span class="btn">Read More</span>
</section>

<section class="services">
  <h2 class="section-title">Our Services</h2>
  <div class="service-grid">
    <div class="service">
      <svg width="40" height="40" viewBox="0 0 40 40"><rect x="8" y="4" width="24" height="34" fill="#333"/><g fill="#eee"><rect x="12" y="9" width="4" height="4"/><rect x="18" y="9" width="4" height="4"/><rect x="24" y="9" width="4" height="4"/><rect x="12" y="17" width="4" height="4"/><rect x="18" y="17" width="4" height="4"/><rect x="24" y="17" width="4" height="4"/><rect x="17" y="28" width="6" height="10"/></g></svg>
      <div><h3>Commercial</h3><p>Lorem ipsum dolor sit amet, consect- etuer adipiscing elit sed diam nonummy.</p></div>
    </div>
    <div class="service">
      <svg width="40" height="40" viewBox="0 0 40 40"><path d="M20 4 2 20h5v16h10V26h6v10h10V20h5z" fill="#333"/></svg>
      <div><h3>Residential</h3><p>Lorem ipsum dolor sit amet, consect- etuer adipiscing elit sed diam nonummy.</p></div>
    </div>
    <div class="service">
      <svg width="40" height="40" viewBox="0 0 40 40"><circle cx="20" cy="16" r="12" fill="#333"/><rect x="18" y="22" width="4" height="16" fill="#333"/><path d="M14 16l6 6 6-8" stroke="#eee" stroke-width="2" fill="none"/></svg>
      <div><h3>Landscape</h3><p>Lorem ipsum dolor sit amet, consect- etuer adipiscing elit sed diam nonummy.</p></div>
    </div>
    <div class="service">
      <svg width="40" height="40" viewBox="0 0 40 40"><rect x="4" y="6" width="32" height="4" fill="#333"/><rect x="7" y="10" width="26" height="18" fill="#333"/><g stroke="#eee" stroke-width="1.5"><line x1="7" y1="15" x2="33" y2="15"/><line x1="7" y1="21" x2="33" y2="21"/></g><line x1="30" y1="28" x2="30" y2="36" stroke="#333" stroke-width="2"/></svg>
      <div><h3>Velmora Shades</h3><p>Lorem ipsum dolor sit amet, consect- etuer adipiscing elit sed diam nonummy.</p></div>
    </div>
    <div class="service">
      <svg width="40" height="40" viewBox="0 0 40 40"><rect x="4" y="12" width="32" height="20" rx="2" fill="#333"/><rect x="8" y="8" width="10" height="4" fill="#333"/><path d="M21 15l-5 8h4l-2 7 6-9h-4l2-6z" fill="#eee"/><rect x="6" y="32" width="4" height="4" fill="#333"/><rect x="30" y="32" width="4" height="4" fill="#333"/></svg>
      <div><h3>Generators</h3><p>Lorem ipsum dolor sit amet, consect- etuer adipiscing elit sed diam nonummy.</p></div>
    </div>
    <div class="service">
      <svg width="40" height="40" viewBox="0 0 40 40"><path d="M20 3a11 11 0 0 0-7 19.5c1.5 1.5 2 3 2 5h10c0-2 .5-3.5 2-5A11 11 0 0 0 20 3z" fill="#333"/><rect x="15" y="29" width="10" height="3" fill="#333"/><rect x="16" y="33" width="8" height="3" fill="#333"/></svg>
      <div><h3>LED Lighting</h3><p>Lorem ipsum dolor sit amet, consect- etuer adipiscing elit sed diam nonummy.</p></div>
    </div>
  </div>
</section>

<section class="gallery">
  <h2 class="section-title">Photo Gallery</h2>
  <div class="tabs"><span class="on">All</span><span>Commercial</span><span>Residential</span><span>Landscape</span></div>
  <div class="photo-grid">
    <div class="photo" role="img" aria-label="Stone residence lit at night" style="background:linear-gradient(180deg,#1e2a44,#5a4632)"></div>
    <div class="photo" role="img" aria-label="Commercial building under a blue sky" style="background:linear-gradient(180deg,#8fb0d0,#8a6a50)"></div>
    <div class="photo" role="img" aria-label="Multi-storey lodge building at twilight" style="background:linear-gradient(180deg,#7e8ea8,#6b4a3a)"></div>
    <div class="photo" role="img" aria-label="Modern home exterior in daylight" style="background:linear-gradient(180deg,#8fb3d6,#b7ab98)"></div>
    <div class="photo" role="img" aria-label="Bright kitchen interior with recessed lighting" style="background:linear-gradient(180deg,#d8d2c6,#8a7d6c)"></div>
    <div class="photo" role="img" aria-label="Home exterior with landscape lighting at night" style="background:linear-gradient(180deg,#24365a,#5a5040)"></div>
  </div>
</section>

<footer class="site-footer">
  <div class="foot-cols">
    <div class="foot-col"><h4>Site Map</h4><ul><li>Home</li><li>Gallery</li><li>Specialty Services</li><li>About</li><li>Contact</li></ul></div>
    <div class="foot-col"><h4>Specialty Services</h4><ul><li>Velmora Housepilot</li><li>Velmora Motorized Shades</li><li>LED Lighting</li><li>Emergency Generators</li></ul></div>
    <div class="foot-col"><h4>Gallery</h4><ul><li>Commercial</li><li>Residential</li><li>Landscape</li></ul></div>
    <div class="foot-col contact"><h4>Contact Info</h4><ul>
      <li><svg width="10" height="14" viewBox="0 0 10 14"><path d="M5 0a5 5 0 0 0-5 5c0 4 5 9 5 9s5-5 5-9a5 5 0 0 0-5-5z" fill="#cfcfcf"/></svg>48 Alder Row, Springvale</li>
      <li>PO Box 120, Springvale 00000</li>
      <li><svg width="12" height="12" viewBox="0 0 12 12"><path d="M2 0h3l1 3-2 1a7 7 0 0 0 4 4l1-2 3 1v3c0 1-1 2-2 2A11 11 0 0 1 0 2c0-1 1-2 2-2z" fill="#cfcfcf"/></svg>(555) 010-0142</li>
      <li><svg width="12" height="10" viewBox="0 0 12 10"><rect width="12" height="10" fill="#cfcfcf"/><path d="M0 0l6 5 6-5" stroke="#1b1b1b" fill="none"/></svg>info@northvaleelectric.example</li>
    </ul></div>
    <div class="foot-col"><h4>Follow Us</h4>
      <div class="social"><b></b><b></b><b></b><b></b><b></b></div>
      <p class="copy">Copyright © 2017 Company Name.<br>All Rights Reserved.</p>
    </div>
  </div>
</footer>

</body>
</html>
```